FunBrixo Business Card

We need a business card design for our company. We sell construction-themed amusement rides for kids.

Contact Information for Business Card

Contact info on business card should include:
Carl Dunning
Co-Founder & COO
(833) 571-FUNBRIX
Carl@funbrixo-demo.com
www.funbrixo-demo.com

```html
<!DOCTYPE html>
<html lang="en">
<head>
<meta charset="utf-8">
<title>FunBrixo Business Card</title>
<link rel="stylesheet" href="https://fonts.googleapis.com/css2?family=Bungee&family=Poppins:wght@400;500;800&display=swap">
<style>
  :root {
    --page-bg: #d9d4cf;
    --band-dark: #1b1b1d;
    --band-mid: #2c2c2f;
    --brand-orange: #e2571f;
    --stripe-orange: #e8692a;
    --stripe-purple: #7a2d8c;
    --stripe-blue: #1f86c8;
    --stripe-pink: #c8195a;
    --panel-light: #efecea;
    --panel-shade: #dcd8d5;
    --name-red: #e2353c;
    --title-blue: #2f7fc1;
    --text-dark: #2e2e33;
    --icon-red: #d63b2f;
    --divider: #c9372d;
    --figure-top: #ead9b6;
    --figure-bottom: #e3c2ae;
  }
  html, body {
    margin: 0;
    width: 1200px;
    height: 969px;
    overflow: hidden;
    background: var(--page-bg);
  }
  .business-card {
    position: absolute;
    left: 100px;
    top: 200px;
    width: 1000px;
    height: 570px;
    border-radius: 20px;
    overflow: hidden;
    background: linear-gradient(180deg, var(--panel-light), var(--panel-shade));
    box-shadow: 0 10px 30px rgba(0,0,0,.18);
  }
  .brand-band {
    position: absolute;
    left: 0; top: 0;
    width: 1000px; height: 265px;
    background: radial-gradient(ellipse at 45% 45%, var(--band-mid), var(--band-dark) 75%);
  }
  .brand-name {
    position: absolute;
    left: 0; right: 0; top: 78px;
    text-align: center;
    font-family: "Poppins", sans-serif;
    font-weight: 800;
    font-size: 92px;
    line-height: 1;
    color: var(--brand-orange);
    letter-spacing: 1px;
  }
  .color-stripes {
    position: absolute;
    left: 0; top: 272px;
    width: 1000px; height: 22px;
    display: flex;
    gap: 4px;
  }
  .color-stripes span { flex: 1; }
  .stripe-orange { background: var(--stripe-orange); }
  .stripe-purple { background: var(--stripe-purple); }
  .stripe-blue { background: var(--stripe-blue); }
  .stripe-pink { background: var(--stripe-pink); }
  .figure-area {
    position: absolute;
    top: 310px;
    width: 124px; height: 245px;
    border-radius: 14px;
    background: linear-gradient(180deg, var(--figure-top), var(--figure-bottom));
  }
  .figure-area-left { left: 8px; }
  .figure-area-right { left: 852px; }
  .identity {
    position: absolute;
    right: 515px; top: 385px;
    text-align: right;
  }
  .person-name {
    font-family: "Bungee", sans-serif;
    font-weight: 400;
    font-size: 34px;
    line-height: 1;
    color: var(--name-red);
    margin: 0;
  }
  .person-title {
    font-family: "Poppins", sans-serif;
    font-weight: 400;
    font-size: 22px;
    color: var(--title-blue);
    margin: 8px 0 0;
  }
  .divider {
    position: absolute;
    left: 503px; top: 385px;
    width: 3px; height: 92px;
    background: var(--divider);
  }
  .contact-list {
    position: absolute;
    left: 530px; top: 383px;
    margin: 0; padding: 0;
    list-style: none;
    font-family: "Poppins", sans-serif;
    font-size: 21px;
    color: var(--text-dark);
  }
  .contact-list li {
    display: flex;
    align-items: center;
    gap: 12px;
    height: 31px;
  }
  .contact-list svg { width: 17px; height: 17px; fill: var(--icon-red); flex: none; }
</style>
</head>
<body>
  <div class="business-card">
    <header class="brand-band">
      <div class="brand-name">FunBrixo</div>
    </header>

    <div class="color-stripes">
      <span class="stripe-orange"></span>
      <span class="stripe-purple"></span>
      <span class="stripe-blue"></span>
      <span class="stripe-pink"></span>
      <span class="stripe-orange"></span>
    </div>

    <div class="figure-area figure-area-left" role="img" aria-label="Cartoon construction worker in hard hat and safety vest"></div>
    <div class="figure-area figure-area-right" role="img" aria-label="Cartoon female construction worker in hard hat with tool belt"></div>

    <div class="identity">
      <h1 class="person-name">CARL DUNNING</h1>
      <p class="person-title">Co-Founder &amp; COO</p>
    </div>

    <div class="divider"></div>

    <ul class="contact-list">
      <li>
        <svg viewBox="0 0 24 24" aria-hidden="true"><path d="M6.6 10.8a15.1 15.1 0 0 0 6.6 6.6l2.2-2.2a1 1 0 0 1 1-.25 11.4 11.4 0 0 0 3.6.57 1 1 0 0 1 1 1V20a1 1 0 0 1-1 1A17 17 0 0 1 3 4a1 1 0 0 1 1-1h3.5a1 1 0 0 1 1 1c0 1.25.2 2.45.57 3.6a1 1 0 0 1-.25 1z"/></svg>
        (833) 571-FUNBRIX
      </li>
      <li>
        <svg viewBox="0 0 24 24" aria-hidden="true"><path d="M2 5h20v14H2z"/><path d="M2 5l10 7 10-7" fill="none" stroke="#efecea" stroke-width="2"/></svg>
        Carl@funbrixo-demo.com
      </li>
      <li>
        <svg viewBox="0 0 24 24" aria-hidden="true"><circle cx="12" cy="12" r="10"/><path d="M2 12h20M12 2c3 3 3 17 0 20M12 2c-3 3-3 17 0 20" fill="none" stroke="#efecea" stroke-width="1.6"/></svg>
        www.funbrixo-demo.com
      </li>
    </ul>
  </div>
</body>
</html>
```